Business Card Design Project

We have recently completed CraftHive projects for a new logo and wesbite.
We now require new business cards.
We hand out very little printed material to clients as all information is online. When we do hand out something, like a business card, we want it to have real impact and make a statement about the quality and professionalism of our company.
We have an idea of what we want our card to look like but we want a designer to make sure they have impact and look great.
Our requirements are…
Size: 85mm X 55mm - Landscape
Front of card: Logo plus the following contact information.
Dennis Marlow
Operations Manager
Phone +44(0) 1632 xxx xxx
Mobile +44(0) 7700 xxx xxx
Email denmo@korvantix.example
Address 17 Pellick Row, Aberdeen AB12 9QZ
Website www.korvantix.example
How you layout the front of the card is up to you, we would like to see some different ideas. Attached are two versions of our logo that may be used.
Back of card: We would like this to be simple but again have impact. Our current thought is to have the logo or just the large W design from the logo in white against a dark background, perhaps made up from the dark green in the logo.
The logos are attached so you can see the colours in them but the dark ones are..
Dark Blue = C:88, M:55, Y:44, K:28
Dark Green = C:87, M:53, Y:50, K:50
We sometimes also use a bright orange as an accent or highlight colour…
Orange: = C:0, M:39, Y:94, K:0

```html
<!DOCTYPE html>
<html lang="en">
<head>
<meta charset="utf-8">
<title>Korvantix Business Cards</title>
<link rel="stylesheet" href="https://fonts.googleapis.com/css2?family=Open+Sans:wght@400;600;700;800&display=swap">
<style>
  :root {
    --stage: #ece8e3;
    --card-white: #ffffff;
    --ink-dark: #22444f;
    --band-dark: #1f5566;
    --grad-from: #3d6e7e;
    --grad-to: #6ca5ab;
    --back-dark: #133f47;
    --mark-muted: #5f8f98;
    --accent-orange: #f0a11c;
    --url-grey: #3a4a55;
    --label: #1d1d1d;
    --white: #ffffff;
  }
  * { box-sizing: border-box; margin: 0; padding: 0; }
  html, body {
    width: 1200px; height: 788px; overflow: hidden;
    background: var(--stage);
    font-family: "Open Sans", sans-serif;
  }
  .sheet { position: relative; width: 1200px; height: 788px; }
  .label {
    position: absolute; width: 200px; text-align: center;
    font-size: 21px; color: var(--label); font-weight: 400;
  }
  .card {
    position: absolute; width: 502px; height: 324px;
    border-radius: 22px; overflow: hidden;
    background: var(--card-white);
  }
  .card--front { left: 83px; top: 57px; }
  .card--back-1 { left: 626px; top: 55px; }
  .card--back-2 { left: 65px; top: 444px; background: var(--back-dark); }
  .card--back-3 { left: 626px; top: 444px; }

  .wordmark {
    position: absolute; left: 0; right: 0;
    display: flex; align-items: center; justify-content: center; gap: 14px;
    color: var(--ink-dark); font-weight: 800; letter-spacing: 1px;
  }
  .wordmark__dot { border-radius: 50%; background: var(--ink-dark); flex: none; }

  .card--front .wordmark { top: 150px; font-size: 40px; }
  .card--front .wordmark__dot { width: 34px; height: 34px; }

  .name-band {
    position: absolute; left: 0; right: 0; top: 207px; height: 34px;
    background: var(--band-dark);
    display: flex; align-items: center; justify-content: center; gap: 6px;
    color: var(--accent-orange);
  }
  .name-band__name { font-weight: 700; font-size: 16px; }
  .name-band__role { font-size: 12px; }
  .divider { position: absolute; left: 0; right: 0; top: 241px; height: 3px; background: #d9e3e6; }
  .contact {
    position: absolute; left: 0; right: 0; top: 244px; bottom: 0;
    background: linear-gradient(100deg, var(--grad-from), var(--grad-to));
    color: var(--white); font-size: 12.5px; text-align: center;
    padding-top: 16px; line-height: 19px;
  }
  .contact b { font-weight: 700; font-style: italic; }

  .card--back-1 .wordmark { top: 96px; font-size: 44px; }
  .card--back-1 .wordmark__dot { width: 38px; height: 38px; }
  .url {
    position: absolute; left: 0; right: 0; text-align: center;
    color: var(--url-grey); font-size: 18px; letter-spacing: 3px;
  }
  .card--back-1 .url { top: 282px; }

  .card--back-2 .wordmark { top: 118px; font-size: 64px; color: var(--mark-muted); }
  .card--back-2 .wordmark__dot { width: 56px; height: 56px; background: var(--mark-muted); }

  .card--back-3 .wordmark { top: 150px; font-size: 50px; }
  .card--back-3 .wordmark__dot { width: 44px; height: 44px; }
  .card--back-3 .url { top: 280px; }
</style>
</head>
<body>
<main class="sheet">
  <div class="label" style="left:220px; top:18px;">Front</div>
  <div class="label" style="left:776px; top:18px;">Back - 1</div>
  <div class="label" style="left:210px; top:402px;">Back - 2</div>
  <div class="label" style="left:776px; top:402px;">Back - 3</div>

  <section class="card card--front">
    <div class="wordmark"><span class="wordmark__dot"></span><span>Korvantix</span></div>
    <div class="name-band">
      <span class="name-band__name">Dennis Marlow,</span>
      <span class="name-band__role">Operations Manager</span>
    </div>
    <div class="divider"></div>
    <div class="contact">
      <p><b>f :</b> +44(0) 1632 xxx xxx | <b>c :</b> +44(0) 7700 xxx xxx</p>
      <p><b>e :</b> denmo@korvantix.example | <b>w :</b> www.korvantix.example</p>
      <p>17 Pellick Row, Aberdeen AB12 9QZ</p>
    </div>
  </section>

  <section class="card card--back-1">
    <div class="wordmark"><span class="wordmark__dot"></span><span>Korvantix</span></div>
    <p class="url">www.korvantix.example</p>
  </section>

  <section class="card card--back-2">
    <div class="wordmark"><span class="wordmark__dot"></span><span>Korvantix</span></div>
  </section>

  <section class="card card--back-3">
    <div class="wordmark"><span class="wordmark__dot"></span><span>Korvantix</span></div>
    <p class="url">www.korvantix.example</p>
  </section>
</main>
</body>
</html>
```